Refresh Brightpath Coursecraft

Need a new design for e-learning development and web app development site: http://brightpathcoursecraft.example. Need pages for everything on menu bar plus a training services and a web app development services pages and a better page for samples http://brightpathcoursecraft.example/samples5/.

***Must be programmed in html 5. NO CMS. No WP. No Plume. Straight html/css.

Target Market(s)

government

Industry/Entity Type

Government

Coding

Coded - Design and coding required

Number of Pages Required

1 page

Requirements
Must have
• Must be coded in html5/css. No CMS.
• Divided so you can easily see that we offer 3 separate services:
• Live Training - E-Learning Development - Web App Development
• A way to display logos of all our clients like on bottom of this page: https://www.quorvatests.example (this is also our website so you can copy all these logos)
• List both our Denver location which is already on our website plus our office in Velmoro Plaza. Street 62 Sur, 14-87. Medellín, Antioquia.
• A page like this for our web app dev services https://www.tekvanu.example/product-development
Should not have
• CMS

```html
<!DOCTYPE html>
<html lang="en">
<head>
<meta charset="utf-8">
<title>Brightpath Coursecraft</title>
<link href="https://fonts.googleapis.com/css2?family=Poppins:wght@300;400;500;600;700&display=swap" rel="stylesheet">
<style>
:root{
  --blue:#2f7fd0;
  --blue-dark:#1f66b3;
  --orange:#f7a32b;
  --orange-deep:#f08c1a;
  --ink:#222;
  --grey:#6d6d6d;
  --line:#e3e3e3;
  --footer:#141414;
  --white:#fff;
}
*{box-sizing:border-box;margin:0;padding:0}
html,body{width:1200px;height:4147px;overflow:hidden}
body{font-family:'Poppins',sans-serif;color:var(--ink);background:var(--white);position:relative}

.site-header{position:absolute;top:0;left:0;width:1200px;height:110px;background:var(--white);display:flex;align-items:center}
.brand{position:absolute;left:112px;top:30px;display:flex;align-items:center;gap:12px}
.brand-mark{width:46px;height:46px;border-radius:50%;background:var(--orange)}
.brand-name{font-size:26px;font-weight:500;color:var(--blue);line-height:1}
.main-nav{position:absolute;left:495px;top:0;height:110px;display:flex;align-items:center;gap:34px;font-size:15px;font-weight:500}
.main-nav a{color:var(--ink);text-decoration:none}
.main-nav .current{color:var(--orange);width:64px;height:64px;border-bottom:3px solid var(--blue);border-radius:50%;display:flex;align-items:flex-end;justify-content:center;padding-bottom:12px;font-size:13px}
.login-btn{position:absolute;left:980px;top:42px;width:106px;height:40px;background:var(--blue);color:var(--white);font-size:14px;font-weight:500;display:flex;align-items:center;justify-content:center;border-bottom:3px solid var(--blue-dark)}

.hero{position:absolute;top:110px;left:0;width:1200px;height:1107px}
.hero svg.backdrop{position:absolute;inset:0}
.hero-title{position:absolute;left:135px;top:290px;font-size:40px;font-weight:500;color:var(--white);line-height:56px;letter-spacing:.3px}
.btn{display:inline-flex;align-items:center;justify-content:center;gap:8px;background:var(--orange);color:var(--white);font-weight:600;text-decoration:none;border-bottom:3px solid var(--orange-deep)}
.hero-btn{position:absolute;left:135px;top:436px;width:175px;height:46px;font-size:15px}
.slide-dots{position:absolute;left:135px;top:532px;display:flex;gap:8px}
.slide-dots i{width:7px;height:7px;border-radius:50%;background:var(--white)}
.slide-dots i.on{background:var(--blue)}
.firm-title{position:absolute;top:708px;width:1200px;text-align:center;color:var(--white);font-size:34px;font-weight:300;line-height:50px}
.firm-text{position:absolute;top:838px;left:186px;width:830px;text-align:center;color:var(--white);font-size:14.5px;line-height:37px}
.firm-text u{text-decoration:underline}
.firm-btn{position:absolute;left:518px;top:1020px;width:164px;height:44px;font-size:14px}

.section-head{position:absolute;width:1200px;text-align:center}
.section-head .ghost{position:absolute;left:0;width:1200px;top:-38px;font-size:92px;font-weight:700;color:#f0f0f0;letter-spacing:2px}
.section-head h2{position:relative;font-size:38px;font-weight:400;color:#111}
.section-head h2 b{font-weight:700}
.services-head{top:1440px}
.clients-head{top:2895px}

.service{position:absolute;left:111px;width:976px;height:334px;border:1px solid var(--line);background:var(--white)}
.service h3{position:absolute;font-size:28px;font-weight:500;color:var(--blue)}
.service p{position:absolute;width:590px;font-size:14.5px;line-height:32.5px;color:var(--grey)}
.service .btn{position:absolute;width:122px;height:36px;font-size:13px}
.service .art{position:absolute;width:230px;height:240px;top:46px;border-radius:12px}
.svc-1{top:1568px}.svc-2{top:1969px}.svc-3{top:2367px}
.txt-left h3{left:54px;top:38px}.txt-left p{left:54px;top:94px}.txt-left .btn{left:54px;top:254px}.txt-left .art{left:700px}
.txt-right h3{left:340px;top:38px}.txt-right p{left:340px;top:94px}.txt-right .btn{left:340px;top:254px}.txt-right .art{left:48px}

.client-grid{position:absolute;top:3033px;left:119px;width:962px;display:grid;grid-template-columns:repeat(6,1fr);border-top:1px solid var(--line);border-left:1px solid var(--line)}
.client{height:133px;border-right:1px solid var(--line);border-bottom:1px solid var(--line);display:flex;flex-direction:column;align-items:center;justify-content:center;gap:8px;font-size:13px;font-weight:500;color:#3a4f7a;text-align:center;padding:0 8px}
.client i{width:40px;height:40px;border-radius:50%;background:#dbe3ef}
.client-dots{position:absolute;top:3487px;left:582px;display:flex;gap:7px}
.client-dots i{width:6px;height:6px;border-radius:50%;background:#bbb}
.client-dots i.on{background:var(--blue)}

.site-footer{position:absolute;top:3595px;left:0;width:1200px;height:552px}
.site-footer svg.top{position:absolute;inset:0}
.footer-mark{position:absolute;left:578px;top:80px;width:46px;height:46px;border-radius:50%;background:var(--orange)}
.office{position:absolute;top:170px;color:var(--white)}
.office h4{font-size:18px;font-weight:600;margin-bottom:24px}
.office-row{display:flex;align-items:center;gap:22px;margin-bottom:24px;font-size:13.5px;line-height:24px}
.office-row svg{flex:none}
.office-1{left:206px}.office-2{left:706px}
.footer-divider{position:absolute;left:599px;top:170px;width:1px;height:255px;background:#3a3a3a}
.footer-rule{position:absolute;top:430px;left:110px;width:980px;height:1px;background:#333}
.social{position:absolute;top:419px;left:498px;display:flex;gap:14px;background:var(--footer);padding:0 6px}
.social span{width:40px;height:40px;border-radius:50%;border:2px solid var(--white)}
.copyright{position:absolute;top:502px;width:1200px;text-align:center;color:var(--white);font-size:13.5px}
</style>
</head>
<body>

<header class="site-header">
  <div class="brand"><span class="brand-mark"></span><span class="brand-name">Brightpath Coursecraft</span></div>
  <nav class="main-nav">
    <a class="current" href="#">HOME</a>
    <a href="#">PORTFOLIO</a>
    <a href="#">TEAM &amp; EXPERIENCE</a>
    <a href="#">CONTACT</a>
  </nav>
  <a class="login-btn" href="#">LOGIN</a>
</header>

<section class="hero">
  <svg class="backdrop" width="1200" height="1107" viewBox="0 0 1200 1107">
    <defs>
      <linearGradient id="heroPhoto" x1="0" y1="0" x2="1" y2="1">
        <stop offset="0" stop-color="#3b3d40"/>
        <stop offset=".55" stop-color="#55585c"/>
        <stop offset="1" stop-color="#8a8d90"/>
      </linearGradient>
    </defs>
    <rect width="1200" height="900" fill="url(#heroPhoto)" role="img" aria-label="Photo of a person working on a laptop with sketched learning icons"/>
    <path d="M0 1075 Q600 1160 1200 1000 L1200 1030 Q600 1190 0 1107 Z" fill="var(--orange)"/>
    <path d="M0 700 Q600 560 1200 725 L1200 1010 Q600 1160 0 1070 Z" fill="var(--blue)"/>
  </svg>
  <h1 class="hero-title">WE CREATE ENGAGING TRAINING<br>THAT EXCEED EXPECTATIONS</h1>
  <a class="btn hero-btn" href="#">READ MORE &#10140;</a>
  <div class="slide-dots"><i></i><i></i><i class="on"></i><i></i><i></i></div>
  <h2 class="firm-title">Instructional Design and<br>Courseware Development Firm</h2>
  <p class="firm-text">Brightpath Coursecraft is a HUBZone Certified, SBA 8(a) Certified, Native American Owned Small Disadvantaged Business located in Denver, Colorado. We have designed and delivered <u>SCORM compliant eLearning, webinar, web-based training (WBT), instructor-led training (ILT), virtual ILT (vILT), blended, and 3D immersive training courses</u>. The Instructional Design Team brings nearly one hundred</p>
  <a class="btn firm-btn" href="#">READ MORE &#10140;</a>
</section>

<div class="section-head services-head"><div class="ghost">OUR SERVICES</div><h2><b>WHAT WE</b> PROVIDE</h2></div>

<article class="service svc-1 txt-left">
  <h3>Live Training</h3>
  <p>Lorem ipsum dolor sit amet, consectetur adipiscing elit. Duis ut dignissim sem. Duis mollis urna sit amet metus gravida vestibulum. In blandit, nit quam conset quam consect maximus fringilla pretium, velit quam consectetur mi, nec suscipit nunc dolor vulputate ante. Pellentesque efficitur id nisi et malesuada.</p>
  <a class="btn" href="#">READ MORE</a>
  <div class="art" role="img" aria-label="Illustration of a trainer presenting online" style="background:linear-gradient(135deg,#dfeefb,#fde6c4)"></div>
</article>

<article class="service svc-2 txt-right">
  <div class="art" role="img" aria-label="Illustration of an e-learning course on a monitor" style="background:linear-gradient(135deg,#fde6c4,#dfeefb)"></div>
  <h3>E-Learning Development</h3>
  <p>Lorem ipsum dolor sit amet, consectetur adipiscing elit. Duis ut dignissim sem. Duis mollis urna sit amet metus gravida vestibulum. In blandit, nit quam conset quam consect maximus fringilla pretium, velit quam consectetur mi, nec suscipit nunc dolor vulputate ante. Pellentesque efficitur id nisi et malesuada.</p>
  <a class="btn" href="#">READ MORE</a>
</article>

<article class="service svc-3 txt-left">
  <h3>Web App Development</h3>
  <p>Lorem ipsum dolor sit amet, consectetur adipiscing elit. Duis ut dignissim sem. Duis mollis urna sit amet metus gravida vestibulum. In blandit, nit quam conset quam consect maximus fringilla pretium, velit quam consectetur mi, nec suscipit nunc dolor vulputate ante. Pellentesque efficitur id nisi et malesuada.</p>
  <a class="btn" href="#">READ MORE</a>
  <div class="art" role="img" aria-label="Illustration of a web app with charts and gears" style="background:linear-gradient(135deg,#dfeefb,#fde6c4)"></div>
</article>

<div class="section-head clients-head"><div class="ghost">OUR CLIENTS</div><h2><b>A FEW OF OUR</b> 75,000 CLIENTS</h2></div>

<div class="client-grid">
  <div class="client"><i></i>Westbrook College</div>
  <div class="client"><i></i>Northfield Corps</div>
  <div class="client"><i></i>Ridgecrest University</div>
  <div class="client"><i></i>Skyline Aviation</div>
  <div class="client"><i></i>Harlow County</div>
  <div class="client">Calveron</div>
  <div class="client">Lumeva</div>
  <div class="client">Aspen Tech Institute</div>
  <div class="client"><i></i>Cedar Ridge Academy</div>
  <div class="client">Harrowgate</div>
  <div class="client">Elmstead University</div>
  <div class="client">Fibrelane</div>
  <div class="client"><i></i>Millbrook College</div>
  <div class="client">Prairie State</div>
  <div class="client"><i></i>Stonegate Seminary</div>
  <div class="client"><i></i>Redfield Fire</div>
  <div class="client"><i></i>Kestrel University</div>
  <div class="client">Oakven</div>
</div>
<div class="client-dots"><i></i><i class="on"></i><i></i></div>

<footer class="site-footer">
  <svg class="top" width="1200" height="552" viewBox="0 0 1200 552">
    <path d="M0 60 Q600 -40 1200 60 L1200 90 Q600 -5 0 90 Z" fill="var(--orange)"/>
    <path d="M0 85 Q600 -10 1200 85 L1200 552 L0 552 Z" fill="var(--footer)"/>
  </svg>
  <span class="footer-mark"></span>

  <div class="office office-1">
    <h4>ADDRESS 1</h4>
    <div class="office-row">
      <svg width="42" height="42" viewBox="0 0 42 42"><circle cx="21" cy="21" r="20" fill="none" stroke="#fff" stroke-width="2"/><path d="M12 21 L21 13 L30 21 H27 V29 H23 V24 H19 V29 H15 V21 Z" fill="#fff"/></svg>
      <div>5830 Larkspur Avenue, Suite 2-140<br>Aurora, CO 80019</div>
    </div>
    <div class="office-row">
      <svg width="42" height="42" viewBox="0 0 42 42"><circle cx="21" cy="21" r="20" fill="none" stroke="#fff" stroke-width="2"/><path d="M15 13 L18 13 L20 18 L18 20 Q20 24 23 25 L25 23 L30 25 L30 28 Q29 30 26 30 Q14 28 13 16 Q13 13 15 13 Z" fill="#fff"/></svg>
      <div>Telephone<br>+1 888 555 0142</div>
    </div>
  </div>
  <div class="footer-divider"></div>
  <div class="office office-2">
    <h4>ADDRESS 2</h4>
    <div class="office-row">
      <svg width="42" height="42" viewBox="0 0 42 42"><circle cx="21" cy="21" r="20" fill="none" stroke="#fff" stroke-width="2"/><path d="M12 21 L21 13 L30 21 H27 V29 H23 V24 H19 V29 H15 V21 Z" fill="#fff"/></svg>
      <div>Velmoro Plaza. Street 62 Sur, 14-87.<br>Medellín, Antioquia</div>
    </div>
    <div class="office-row">
      <svg width="42" height="42" viewBox="0 0 42 42"><circle cx="21" cy="21" r="20" fill="none" stroke="#fff" stroke-width="2"/><path d="M15 13 L18 13 L20 18 L18 20 Q20 24 23 25 L25 23 L30 25 L30 28 Q29 30 26 30 Q14 28 13 16 Q13 13 15 13 Z" fill="#fff"/></svg>
      <div>Phone :<br>1 888 555 0199</div>
    </div>
  </div>

  <div class="footer-rule"></div>
  <div class="social" aria-label="Social links">
    <span aria-label="Social link 1"></span><span aria-label="Social link 2"></span><span aria-label="Social link 3"></span><span aria-label="Social link 4"></span>
  </div>
  <p class="copyright">© copyright 2018 Brightpath Coursecraft.All Rights Reserved &nbsp;|&nbsp; Privacy policy</p>
</footer>

</body>
</html>
```